Carwash Signage

We own and operate a 25m tunnel car wash in the uk. We are looking to upgrade our signage to include the following:-

Wash selection Board Size-1300x1300mm
Conditions 1300x1300mm
Instructions 1300x1300mm
Banner 2600x600mm
Stamp card flyer a5 double sided - 9 squares for stamping 3rd square needs to say free air freshener 9th square needs to say free vip car wash.

I have attached some notes for the details that are required to be included.

We are looking for a modern smart look more European car wash style than American car wash style. It should be bold and clear. with yellow/orange & blue/green,grey colours

The final design must be in a industry standard printable format.

UPDATED BRIEF AS DISCUSSED: We require design for 2 x window decals, flag design and 50% off voucher. Attached are rough layout drawings of what they should look like - we expect the designs to be in keeping with the previous designs colours, etc that have been carried out. We Look forward to hearing from you.

Target Market(s)

local car owners within a 15-20 mile radius

Colors
0054AA
0677BA
7BADD7
CADEEF
E8F1F8
0094D4
00A9DD
6FCCEA
C7EBF8
E9F6FB
00AB8E
00BBA5
67D7C9
C6EFE9
E9F9F6

Requirements
Must have
• must be sharp and modern European look

```html
<!DOCTYPE html>
<html lang="en">
<head>
<meta charset="utf-8">
<title>Attended Car Wash Banner</title>
<link href="https://fonts.googleapis.com/css2?family=Montserrat:wght@600;800&family=Roboto:wght@700&display=swap" rel="stylesheet">
<style>
  :root {
    --backdrop: #bdbabb;
    --banner-navy: #243c50;
    --sign-yellow: #f5b81c;
    --sign-white: #ffffff;
    --brand-blue: #2a5fa5;
    --pay-navy: #263a8c;
    --pay-red: #e8332a;
    --pay-blue: #2f73c3;
    --pay-sky: #2f8fd8;
  }
  * { margin: 0; padding: 0; box-sizing: border-box; }
  html, body {
    width: 1200px;
    height: 480px;
    overflow: hidden;
    background: var(--backdrop);
  }
  .banner {
    position: absolute;
    left: 58px;
    top: 115px;
    width: 1083px;
    height: 250px;
    background: var(--banner-navy);
    color: var(--sign-white);
    font-family: "Montserrat", sans-serif;
  }
  .banner__kicker {
    position: absolute;
    left: 18px;
    top: 17px;
    font-size: 49px;
    font-weight: 600;
    line-height: 1;
    letter-spacing: 0.5px;
  }
  .banner__headline {
    position: absolute;
    left: 280px;
    top: 80px;
    font-size: 92px;
    font-weight: 800;
    line-height: 1;
    color: var(--sign-yellow);
    letter-spacing: 1px;
    white-space: nowrap;
  }
  .brand-panel {
    position: absolute;
    left: 842px;
    top: 9px;
    width: 231px;
    height: 80px;
    background: var(--sign-white);
    display: flex;
    align-items: center;
    justify-content: center;
    gap: 10px;
    color: var(--brand-blue);
    font-weight: 800;
  }
  .brand-panel__dot {
    width: 22px;
    height: 22px;
    border-radius: 50%;
    background: var(--brand-blue);
  }
  .brand-panel__name {
    font-size: 21px;
    line-height: 1.05;
    letter-spacing: 0.5px;
  }
  .brand-panel__name small {
    display: block;
    font-size: 12px;
    letter-spacing: 2px;
    text-align: right;
  }
  .payment {
    position: absolute;
    left: 20px;
    top: 210px;
    display: flex;
    align-items: center;
  }
  .payment__label {
    font-family: "Roboto", sans-serif;
    font-weight: 700;
    font-size: 24px;
    color: var(--sign-yellow);
    white-space: nowrap;
    margin-right: 28px;
  }
  .payment__methods { display: flex; align-items: center; gap: 8px; }
  .payment__method { width: 40px; height: 26px; border-radius: 2px; }
  .payment__method--navy { background: var(--pay-navy); }
  .payment__method--red { background: var(--pay-red); border-radius: 50%; width: 30px; height: 30px; margin: 0 6px; }
  .payment__method--blue { background: var(--pay-blue); height: 29px; }
  .payment__method--sky { background: var(--pay-sky); border-radius: 50%; width: 30px; height: 30px; margin: 0 4px; }
  .payment__method--wide { background: var(--pay-blue); width: 48px; height: 14px; }
  .opening-hours {
    position: absolute;
    left: 857px;
    top: 172px;
    width: 200px;
    text-align: center;
    font-size: 19px;
    font-weight: 600;
    line-height: 22.5px;
    white-space: nowrap;
    display: flex;
    flex-direction: column;
    align-items: center;
  }
</style>
</head>
<body>
  <section class="banner">
    <p class="banner__kicker">ATTENDED</p>
    <h1 class="banner__headline">CAR WASH</h1>

    <div class="brand-panel">
      <span class="brand-panel__dot"></span>
      <p class="brand-panel__name"><small>CAR WASH</small>HARBOURLINE</p>
    </div>

    <div class="payment">
      <p class="payment__label">CASH / CARD PAYMENT ACCEPTED</p>
      <div class="payment__methods" role="img" aria-label="Accepted payment methods">
        <span class="payment__method payment__method--navy"></span>
        <span class="payment__method payment__method--red"></span>
        <span class="payment__method payment__method--blue"></span>
        <span class="payment__method payment__method--sky"></span>
        <span class="payment__method payment__method--wide"></span>
      </div>
    </div>

    <div class="opening-hours">
      <span>OPENING:</span>
      <span>MON - SAT 8:00 TO 18:00</span>
      <span>SUN 9:00 TO 18:00</span>
    </div>
  </section>
</body>
</html>
```